Business Cards Design for the electrical wholesaler: clean bold dynamic :)

We need a business card design that would follow our latest brand guidelines. As an electrical wholesaler we want to bring a fresh look and feel into the industry. The design should be clean bold and dynamic. It should come alive with the renewed energy of our green colour. Our grey colour should keep things balanced and complement the notion of maturity and responsibility. We employ Lato as a corporate font however are not bound by this font and we’re open to interpretation here.

Target Market(s)

Electrical contractors

Industry/Entity Type

Business

Contact Information for Business Card

Logo
Name & Surname: Halyna Dorosh
Job Title: Director of Marketing
Email: halya.dorosh@quillmail.example
Cell phone: XXX.XXX.XXXX
Address: 20517 - 87 Ave. Edmonton, AB, Canada. T6K 4N8
Business Phone: 780.555.0184
Website: www.brovix.example

Font styles to use
Other font styles liked:
• Lato

Requirements
Must have
• Logo & website
Nice to have
• Brand elements - some of them you may find in the attached Brand Guidelines (e.g. three lines on the background signifying "W")

```html
<!DOCTYPE html>
<html lang="en">
<head>
<meta charset="utf-8">
<title>Brovix Business Card</title>
<link href="https://fonts.googleapis.com/css2?family=Lato:wght@400;700;900&display=swap" rel="stylesheet">
<style>
  :root {
    --backdrop: #2b2b2b;
    --card-dark: #262626;
    --card-light: #ffffff;
    --brand-green: #8cc63f;
    --brand-grey: #58595b;
    --text-dark: #3a3a3a;
    --rule: #b5b5b5;
  }
  * { margin: 0; padding: 0; box-sizing: border-box; }
  html, body {
    width: 1200px; height: 900px; overflow: hidden;
    background: var(--backdrop);
    font-family: "Lato", sans-serif;
  }
  .card {
    position: absolute; left: 280px;
    width: 640px; height: 366px;
    border-radius: 18px; overflow: hidden;
  }
  .card--front { top: 50px; background: var(--card-dark); }
  .card--back { top: 480px; background: var(--card-light); }

  .wordmark {
    display: flex; align-items: center; gap: 14px;
    font-weight: 900; letter-spacing: 1px;
  }
  .wordmark__square { display: block; }
  .card--front .wordmark {
    position: absolute; left: 0; right: 0; top: 0; bottom: 0;
    justify-content: center; font-size: 76px; color: #e4e4e4;
  }
  .card--front .wordmark__square { width: 52px; height: 52px; background: #e4e4e4; }

  .card--back .wordmark {
    position: absolute; left: 48px; top: 40px;
    font-size: 58px; color: var(--brand-grey);
  }
  .card--back .wordmark__square { width: 40px; height: 40px; background: var(--brand-green); }

  .divider {
    position: absolute; left: 48px; right: 48px; top: 208px;
    height: 1px; background: var(--rule);
  }
  .person { position: absolute; left: 48px; top: 148px; }
  .person__name { font-size: 30px; font-weight: 900; color: var(--brand-green); line-height: 1; }
  .person__title { font-size: 17px; color: var(--text-dark); margin-top: 6px; }

  .contacts { position: absolute; left: 48px; top: 224px; list-style: none; }
  .contacts li {
    display: flex; align-items: center; gap: 12px;
    font-size: 17px; color: var(--text-dark); height: 26px;
  }
  .contacts svg { width: 16px; height: 16px; flex: none; }

  .address {
    position: absolute; right: 48px; top: 226px;
    text-align: right; font-size: 16px; line-height: 1.4; color: var(--text-dark);
  }

  .footer-shape { position: absolute; left: 0; bottom: 0; width: 640px; height: 90px; }
  .website {
    position: absolute; right: 40px; bottom: 24px;
    font-size: 15px; letter-spacing: 3px; color: #ffffff;
  }
</style>
</head>
<body>
  <section class="card card--front">
    <div class="wordmark"><span class="wordmark__square"></span>brovix</div>
  </section>

  <section class="card card--back">
    <div class="wordmark"><span class="wordmark__square"></span>brovix</div>

    <div class="person">
      <p class="person__name">Halyna Dorosh</p>
      <p class="person__title">Director of Marketing</p>
    </div>
    <div class="divider"></div>

    <ul class="contacts">
      <li>
        <svg viewBox="0 0 16 16" aria-hidden="true"><rect x="4" y="1" width="8" height="14" rx="1.5" fill="none" stroke="#8cc63f" stroke-width="1.6"/><line x1="7" y1="12.5" x2="9" y2="12.5" stroke="#8cc63f" stroke-width="1.4"/></svg>
        780.555.0184
      </li>
      <li>
        <svg viewBox="0 0 16 16" aria-hidden="true"><path d="M3 2 L6 2 L7 5.5 L5.3 6.8 C6.3 8.8 7.7 10.2 9.5 11 L10.8 9.3 L14 10.3 L14 13.2 C14 13.8 13.5 14.2 12.9 14.2 C7 13.8 2.4 9.2 2 3.2 C2 2.6 2.4 2 3 2 Z" fill="#8cc63f"/></svg>
        780.555.0184
      </li>
      <li>
        <svg viewBox="0 0 16 16" aria-hidden="true"><rect x="1" y="3" width="14" height="10" rx="1" fill="#8cc63f"/><path d="M1.5 3.5 L8 9 L14.5 3.5" fill="none" stroke="#ffffff" stroke-width="1.4"/></svg>
        halya.dorosh@quillmail.example
      </li>
    </ul>

    <p class="address">20517 - 87 Ave. Edmonton<br>AB, Canada. T6K 4N8</p>

    <svg class="footer-shape" viewBox="0 0 640 90" aria-hidden="true">
      <rect x="0" y="78" width="640" height="12" fill="#8cc63f"/>
      <path d="M0 46 H398 C425 46 428 16 458 16 H640 V78 H0 V54 H398 C402 54 404 54 406 54 Z" fill="#ffffff" opacity="0"/>
      <path d="M0 44 H392 L394 52 H0 Z" fill="#8cc63f"/>
      <path d="M392 44 C422 44 426 14 458 14 H640 V78 H394 V52 Z" fill="#262626"/>
    </svg>
    <p class="website">www.brovix.example</p>
  </section>
</body>
</html>
```